Stylish Business Cards Wanted

- DOUBLE SIDED Design Required -

High end, edgy cards for a corporate and personal stylist. Must include logo,
Name: Belinda Harwick
Title: Director and Stylist
telephone : +61 8 7142 5809
email: belinda@theloombriefing.example
website: theloombriefing.example
Tag: Corporate Workwear & Uniform Specialist | Personal Stylist
Would like nice icons for telephone, email, website

Target Market(s)

Businesses wanting stylish uniforms, people wanting stylish wardrobes

Industry/Entity Type

Corporate Workwear Stylist

Contact Information for Business Card

I would like black, white and gold foiling incorporated in the design - possibly a touch of the other colours on my branding guide attached Name: Belinda Harwick Title: Director and Stylist telephone : +61 8 7142 5809 email: belinda@theloombriefing.example website: theloombriefing.example Tag: Corporate Workwear & Uniform Specialist | Personal Stylist Would like nice icons for telephone, email, website

Font styles to use
Other font styles liked:
• Raleway

Colors

Designer to choose colors to be used in the design.

Requirements
Must have
• Gold foil accents

```html
<!DOCTYPE html>
<html lang="en">
<head>
<meta charset="utf-8">
<title>Belinda Harwick – Business Card</title>
<link href="https://fonts.googleapis.com/css2?family=Norican&family=Roboto:wght@400;500&display=swap" rel="stylesheet">
<style>
  :root {
    --backdrop: #e8e2da;
    --card: #f8f6f3;
    --navy: #1d2236;
    --gold: #c9a24a;
    --gold-light: #e2c77d;
    --pink: #d8175f;
    --ink: #1f2230;
  }
  html, body {
    margin: 0;
    width: 1200px;
    height: 1054px;
    overflow: hidden;
    background: var(--backdrop);
  }
  .card {
    position: absolute;
    left: 100px;
    top: 227px;
    width: 1000px;
    height: 600px;
    background: var(--card);
    border-radius: 26px;
    overflow: hidden;
    box-shadow: 0 18px 40px rgba(0,0,0,.12);
    font-family: "Roboto", Arial, sans-serif;
    color: var(--ink);
  }
  .footer-band {
    position: absolute;
    left: 0;
    right: 0;
    bottom: 0;
    height: 100px;
    background: var(--navy);
  }
  .gold-rule {
    position: absolute;
    left: 0;
    right: 0;
    bottom: 110px;
    height: 5px;
    background: var(--gold);
  }
  .accent-dot {
    position: absolute;
    left: -40px;
    top: 78px;
    width: 60px;
    height: 120px;
    border-radius: 0 60px 60px 0;
    background: var(--pink);
  }
  .name {
    position: absolute;
    left: 52px;
    top: 70px;
    margin: 0;
    font-family: "Norican", cursive;
    font-weight: 400;
    font-size: 54px;
    line-height: 1.2;
    color: var(--gold);
  }
  .title {
    position: absolute;
    left: 53px;
    top: 148px;
    margin: 0;
    font-size: 25px;
  }
  .contact {
    position: absolute;
    left: 53px;
    top: 250px;
    margin: 0;
    padding: 0;
    list-style: none;
    font-size: 25px;
  }
  .contact li {
    display: flex;
    align-items: center;
    gap: 18px;
    height: 50px;
  }
  .contact li.social { margin-bottom: 16px; gap: 14px; }
  .social-mark {
    width: 22px; height: 22px;
    border-radius: 5px;
    background: var(--gold);
  }
  .contact svg { width: 26px; height: 26px; flex: none; }
  .brand {
    position: absolute;
    right: 80px;
    top: 100px;
    width: 330px;
    margin: 0;
    text-align: center;
    font-weight: 500;
    font-size: 58px;
    line-height: 1.05;
    color: var(--navy);
    letter-spacing: 1px;
  }
  .services {
    position: absolute;
    right: 30px;
    bottom: 8px;
    margin: 0;
    padding: 0;
    list-style: none;
    text-align: right;
    font-family: "Norican", cursive;
    font-size: 24px;
    line-height: 28px;
    color: var(--gold-light);
  }
  .services li { height: 28px; }
  .services li::after {
    content: "«";
    font-family: "Roboto", Arial, sans-serif;
    color: var(--pink);
    margin-left: 18px;
    font-size: 22px;
  }
</style>
</head>
<body>
  <section class="card">
    <span class="gold-rule"></span>
    <span class="footer-band"></span>
    <span class="accent-dot"></span>

    <h1 class="name">Belinda Harwick</h1>
    <p class="title">Director and Stylist</p>

    <ul class="contact">
      <li class="social"><span class="social-mark"></span>/theloombriefing101</li>
      <li>
        <svg viewBox="0 0 24 24" fill="none" stroke="var(--gold)" stroke-width="1.8"><circle cx="12" cy="12" r="10"/><path d="M9 7.5l1.6 2.6-1.2 1.3c.7 1.4 1.8 2.5 3.2 3.2l1.3-1.2 2.6 1.6-.9 1.7c-3.6-.3-7.4-4.1-7.7-7.7z" fill="var(--gold)" stroke="none"/></svg>
        +61 8 7142 5809
      </li>
      <li>
        <svg viewBox="0 0 24 24" fill="none" stroke="var(--gold)" stroke-width="1.8"><rect x="2.5" y="5" width="19" height="14" rx="1.5"/><path d="M3 6l9 7 9-7"/></svg>
        belinda@theloombriefing.example
      </li>
      <li>
        <svg viewBox="0 0 24 24" fill="var(--gold)"><circle cx="12" cy="12" r="10"/><g fill="none" stroke="var(--card)" stroke-width="1.3"><ellipse cx="12" cy="12" rx="4" ry="10"/><path d="M2 12h20M4 7h16M4 17h16"/></g></svg>
        theloombriefing.example
      </li>
    </ul>

    <p class="brand">The Loom Briefing</p>

    <ul class="services">
      <li>Personal Stylist</li>
      <li>Corporate Workwear</li>
      <li>and Uniform Specialist</li>
    </ul>
  </section>
</body>
</html>
```